Business card

We need a business card design for our company based in Auckland , New Zealand called 'Ridge + Studio Ltd'. We provide architectural services. We would like to see designs that use the max. three colours (such as white, black, grey) The final design should communicate financial safety and growth."
Also I will provide our company logo. I would like to the logo to be embeded onto our business card.

Target Market(s)

new residential house, alteration & addition & light commericila design & drafting service

Industry/Entity Type

Architecture

Contact Information for Business Card

Company name: ridge + studio Ltd.
Name: Mark Delford
Job title: architectural designer & Design LBP
email address: mark@rplusd.co.nz
mobile number: 02 5163 2290
web site: www.rplusd.co.nz

Requirements
Must have
• My project must have..
• - embeded logo (attached company logo)
• I don't have a bigger version for our company logo, but I have one old one, so you can remove the word from it)
• - insert the attached small BKTW logo & LBP logo
• - creative, simple and clear business card.
• - Max. three colours
Nice to have
• - Here are the samples I would like to share with you: http://www.plimvora.com/blog/minimalistic-business-card-designs/
• I would like to have my business card like one of the creation.
Should not have
• TBA

```html
<!DOCTYPE html>
<html lang="en">
<head>
<meta charset="utf-8">
<title>Ridge + Studio Ltd. – Business Card</title>
<link rel="stylesheet" href="https://fonts.googleapis.com/css2?family=Open+Sans:wght@400;600&family=Cinzel:wght@400&display=swap">
<style>
  :root {
    --card: #1f2a35;
    --ink: #ffffff;
    --ink-soft: #eef0f2;
    --backdrop: #ebebeb;
  }
  * { margin: 0; padding: 0; box-sizing: border-box; }
  html, body { width: 1200px; height: 900px; overflow: hidden; }
  body {
    position: relative;
    background: var(--backdrop);
    font-family: "Open Sans", Arial, sans-serif;
    color: var(--ink);
  }
  .card {
    position: absolute;
    background: var(--card);
    box-shadow: 0 6px 18px rgba(0,0,0,.25);
  }
  .card--front { left: 238px; top: 62px; width: 555px; height: 343px; }
  .card--back  { left: 458px; top: 518px; width: 560px; height: 343px; }

  /* front: brand mark area */
  .brand-mark {
    position: absolute;
    left: 72px; top: 84px;
    width: 180px; height: 172px;
    display: flex; flex-direction: column;
    align-items: center; justify-content: center; gap: 12px;
  }
  .brand-mark__dot {
    width: 34px; height: 34px; border-radius: 50%;
    background: var(--ink);
  }
  .brand-mark__name {
    font-size: 17px; font-weight: 600; color: var(--ink);
    white-space: nowrap;
  }

  /* front: person */
  .person { position: absolute; left: 274px; top: 94px; }
  .person__name { font-size: 19px; font-weight: 600; line-height: 1.2; }
  .person__role { font-size: 14.5px; color: var(--ink-soft); line-height: 1.3; }

  .contact-list {
    position: absolute; left: 274px; top: 186px;
    list-style: none;
  }
  .contact-list__item {
    display: flex; align-items: center; gap: 9px;
    font-size: 14.5px; line-height: 20px; color: var(--ink-soft);
  }
  .contact-list__icon { width: 11px; height: 11px; fill: var(--ink); flex: none; }

  /* back */
  .back-mark {
    position: absolute; left: 227px; top: 48px;
    width: 104px; height: 104px; border-radius: 50%;
    border: 7px solid var(--ink);
  }
  .company-name {
    position: absolute; left: 0; right: 0; top: 156px;
    text-align: center;
    font-family: "Cinzel", Georgia, serif;
    font-size: 20px; letter-spacing: .6px;
    white-space: nowrap;
    text-shadow: 0 2px 3px rgba(0,0,0,.5);
  }
  .badges { position: absolute; left: 165px; top: 214px; display: flex; align-items: center; gap: 18px; }
  .badge--member { width: 112px; height: 88px; background: var(--ink); border-radius: 4px; }
  .badge--cert { width: 100px; height: 100px; border-radius: 50%; background: var(--ink); }
</style>
</head>
<body>

<section class="card card--front" aria-label="Business card front">
  <div class="brand-mark">
    <span class="brand-mark__dot"></span>
    <span class="brand-mark__name">Ridge + Studio Ltd.</span>
  </div>

  <div class="person">
    <p class="person__name">Mark Delford</p>
    <p class="person__role">Architectural designer &amp; Design LBP</p>
  </div>

  <ul class="contact-list">
    <li class="contact-list__item">
      <svg class="contact-list__icon" viewBox="0 0 24 24" aria-hidden="true"><path d="M6.6 10.8a15.1 15.1 0 0 0 6.6 6.6l2.2-2.2a1 1 0 0 1 1-.25 11.4 11.4 0 0 0 3.6.57 1 1 0 0 1 1 1V20a1 1 0 0 1-1 1A17 17 0 0 1 3 4a1 1 0 0 1 1-1h3.5a1 1 0 0 1 1 1c0 1.25.2 2.45.57 3.57a1 1 0 0 1-.25 1z"/></svg>
      02 5163 2290
    </li>
    <li class="contact-list__item">
      <svg class="contact-list__icon" viewBox="0 0 24 24" aria-hidden="true"><path d="M2 5h20v14H2zm2 2v.5l8 5 8-5V7l-8 5z"/></svg>
      mark@rplusd.co.nz
    </li>
    <li class="contact-list__item">
      <svg class="contact-list__icon" viewBox="0 0 24 24" aria-hidden="true"><path d="M12 2a10 10 0 1 0 0 20 10 10 0 0 0 0-20zm-1 17.9A8 8 0 0 1 4.1 11H7l2 2v2l2 2zM17.9 16.4 16 14h-2v-3l-3-3 2-2V4.1a8 8 0 0 1 4.9 12.3z"/></svg>
      www.rplusd.co.nz
    </li>
  </ul>
</section>

<section class="card card--back" aria-label="Business card back">
  <span class="back-mark"></span>
  <p class="company-name">RIDGE + STUDIO LTD.</p>
  <div class="badges">
    <span class="badge--member" role="img" aria-label="Professional membership badge"></span>
    <span class="badge--cert" role="img" aria-label="Certification badge"></span>
  </div>
</section>

</body>
</html>
```